Meridale Bed Company Needs Business Card

Looking for a very nice looking business card. Creative but not extravagant. We sell beds and pillows across the U.S. and need something professional but catchy. I have attached the logo.

Name : Devin Holt
Title : President
Phone : (800) 471-2960
Email: sleep@quilmora.com
Website: www.quilmora.com

Can be single-sided or double-sided
horizontal or vertical

Can use Blues/Greys

Target Market(s)

Mass Market

Industry/Entity Type

Retail

Contact Information for Business Card

Name : Devin Holt
Title : President
Phone : (800) 471-2960
Email: sleep@quilmora.com
Website: www.quilmora.com

Requirements
Must have
• Clean, Modern, Smooth
• Can use Blues/Greys
• On the other side without the information - have something simple like www.quilmora.com or our logo
Nice to have
• Surprise me
Should not have
• Nothing crazy, nothing cluttered

```html
<!DOCTYPE html>
<html lang="en">
<head>
<meta charset="UTF-8">
<title>Quilmora Business Card</title>
<link href="https://fonts.googleapis.com/css2?family=Montserrat:wght@300;400;700&display=swap" rel="stylesheet">
<style>
  :root {
    --bg: #e7e9ec;
    --card: #070707;
    --card-sheen: #2a2b2d;
    --blue: #3fa9e0;
    --white: #f2f2f2;
    --grey: #bfc3c7;
  }
  * { margin: 0; padding: 0; box-sizing: border-box; }
  html, body {
    width: 1200px; height: 913px; overflow: hidden;
    background: var(--bg);
    font-family: "Montserrat", sans-serif;
  }
  .stage {
    position: relative; width: 1200px; height: 913px;
    display: flex; align-items: center; justify-content: center; gap: 60px;
  }
  .card {
    position: relative; width: 525px; height: 300px;
    background:
      linear-gradient(110deg, transparent 38%, rgba(255,255,255,0.06) 46%, rgba(255,255,255,0.12) 52%, rgba(255,255,255,0.04) 60%, transparent 70%),
      radial-gradient(ellipse at 55% 40%, var(--card-sheen) 0%, var(--card) 65%);
    border-radius: 3px;
    box-shadow: 0 14px 30px rgba(0,0,0,0.28), 0 3px 6px rgba(0,0,0,0.2);
    overflow: hidden;
  }
  .brand-name {
    position: absolute;
    font-family: "Montserrat", sans-serif;
    font-weight: 300;
    color: var(--blue);
    letter-spacing: 1px;
    line-height: 1;
    white-space: nowrap;
  }
  /* Front */
  .card-front .brand-name { left: 34px; top: 104px; font-size: 56px; }
  .name-block {
    position: absolute; right: 34px; top: 146px; text-align: right;
  }
  .person-name { color: var(--blue); font-weight: 700; font-size: 20px; letter-spacing: 0.3px; line-height: 1.1; }
  .person-title { color: var(--white); font-weight: 400; font-size: 11px; margin-top: 3px; }
  .tab-white, .tab-blue {
    position: absolute; right: 0; width: 16px; height: 20px;
  }
  .tab-white { top: 140px; background: var(--white); }
  .tab-blue { top: 160px; background: var(--blue); }
  .divider {
    position: absolute; left: 150px; right: 30px; top: 192px;
    height: 1px; background: var(--grey);
  }
  .contact-list {
    position: absolute; left: 150px; top: 206px; list-style: none;
  }
  .contact-list li {
    display: flex; align-items: center; gap: 8px;
    color: var(--white); font-size: 13px; font-weight: 300;
    line-height: 20px; letter-spacing: 0.3px;
  }
  .contact-list svg { width: 10px; height: 10px; flex: none; }
  /* Back */
  .card-back .brand-name { left: 0; right: 0; text-align: center; top: 108px; font-size: 86px; }
  .back-url {
    position: absolute; right: 48px; top: 222px;
    color: var(--white); font-size: 14px; font-weight: 300; letter-spacing: 1px;
  }
  .back-url .accent { color: var(--blue); }
</style>
</head>
<body>
<main class="stage">
  <section class="card card-front" aria-label="Business card front">
    <div class="brand-name">quilmora</div>
    <div class="tab-white"></div>
    <div class="tab-blue"></div>
    <div class="name-block">
      <div class="person-name">Devin Holt</div>
      <div class="person-title">President</div>
    </div>
    <div class="divider"></div>
    <ul class="contact-list">
      <li>
        <svg viewBox="0 0 10 10" aria-hidden="true"><path d="M2 1 L4 1 L4.5 3 L3.3 4 Q4.3 6 6 6.7 L7 5.5 L9 6 L9 8 Q5 9 2.5 6 Q0.8 3.5 2 1 Z" fill="var(--blue)"/></svg>
        (800) 471-2960
      </li>
      <li>
        <svg viewBox="0 0 10 10" aria-hidden="true"><rect x="0.5" y="2" width="9" height="6.5" fill="none" stroke="var(--blue)" stroke-width="1.2"/><path d="M0.5 2 L5 6 L9.5 2" fill="none" stroke="var(--blue)" stroke-width="1.2"/></svg>
        sleep@quilmora.com
      </li>
      <li>
        <svg viewBox="0 0 10 10" aria-hidden="true"><circle cx="5" cy="5" r="4.3" fill="none" stroke="var(--blue)" stroke-width="1.1"/><ellipse cx="5" cy="5" rx="1.8" ry="4.3" fill="none" stroke="var(--blue)" stroke-width="0.9"/><line x1="0.7" y1="5" x2="9.3" y2="5" stroke="var(--blue)" stroke-width="0.9"/></svg>
        www.quilmora.com
      </li>
    </ul>
  </section>

  <section class="card card-back" aria-label="Business card back">
    <div class="brand-name">quilmora</div>
    <div class="back-url">www.<span class="accent">quilmora</span>.com</div>
  </section>
</main>
</body>
</html>
```